Quorbelline.io - Please redesign to make it look better from current design

We already have the current website, that you can access but we think it can improve from current version.
Quorbelline is a cryptocurrency hedge fund that allow you to participate in the hedge fund with cryptocurrency such as eth.
At current phase, we are doing an ICO, then we want to make sure that the website it looks professional, beautiful and trustable enough for investors after looking at our website.
Target Market(s)
Investors
Industry/Entity Type
Investment
Coding
Coded - Design and coding required
Number of Pages Required
1 page
Look and feel
Each slider illustrates characteristics of the customer's brand and the style your logo design should communicate.

```html
<!DOCTYPE html>
<html lang="en">
<head>
<meta charset="utf-8">
<title>Quorbelline.io – Digital Asset Management</title>
<link href="https://fonts.googleapis.com/css2?family=Jost:wght@400;500;600;700&family=Mulish:wght@400;600;700&display=swap" rel="stylesheet">
<style>
:root{
  --navy:#0c2a6e;
  --navy-deep:#081f55;
  --navy-soft:#1a3a85;
  --ink:#0b2160;
  --text:#5b6275;
  --muted:#8a8f9c;
  --white:#ffffff;
  --paper:#efefef;
  --black:#050608;
}
*{margin:0;padding:0;box-sizing:border-box}
html,body{width:1200px;height:3659px;overflow:hidden}
body{font-family:"Mulish",sans-serif;color:var(--text);background:var(--white);position:relative}
.abs{position:absolute}
.heading{font-family:"Jost",sans-serif}
.pill{position:absolute;border-radius:40px;font-family:"Jost",sans-serif;font-weight:500;text-transform:uppercase;display:flex;align-items:center;justify-content:center;letter-spacing:.5px}
.pill-solid{background:var(--navy);color:var(--white);border:3px solid #3f63b5;box-shadow:0 6px 14px rgba(0,0,0,.25)}
.pill-outline{border:2px solid var(--white);color:var(--white)}

/* header */
.site-header{left:0;top:0;width:1200px;height:127px;background:var(--navy)}
.brand{display:flex;align-items:center;gap:12px;color:var(--white);font-family:"Jost",sans-serif;font-weight:600;font-size:30px}
.brand-dot{width:22px;height:22px;border-radius:50%;background:var(--white)}
.main-nav{right:320px;top:48px;display:flex;gap:28px;font-family:"Jost",sans-serif;font-size:18px;color:var(--white);text-transform:uppercase}

/* hero */
.hero{left:0;top:127px;width:1200px;height:551px;background:linear-gradient(100deg,#2e3646 0%,#6e7784 45%,#c9cdd2 70%,#8a8f98 100%)}
.hero-title{left:78px;top:265px;font-family:"Jost",sans-serif;font-weight:700;font-size:70px;line-height:78px;color:var(--white);text-transform:uppercase;letter-spacing:1px}
.hero-copy{left:78px;top:410px;width:620px;font-size:16px;line-height:25px;color:#e8ebf0;font-style:italic}

/* info band */
.info-band{left:0;top:678px;width:1200px;height:262px}
.info-title{left:205px;top:730px;font-size:42px;font-weight:500;color:var(--white)}
.info-copy{left:205px;top:790px;width:640px;font-size:14px;line-height:25px;color:#c9d2ea}

/* definition */
.def-title{left:78px;top:985px;font-size:42px;font-weight:500;color:var(--ink)}
.def-copy{left:78px;top:1050px;width:540px;font-size:14px;line-height:25px}
.def-copy p+p{margin-top:12px}
.def-media{left:668px;top:951px;width:454px;height:354px}

/* process */
.process{left:0;top:1378px;width:1200px;height:739px;background:linear-gradient(180deg,#0c2a6e 0%,#1b3c86 55%,#0c2a6e 100%)}
.process-title{left:0;width:1200px;top:1430px;text-align:center;font-size:42px;font-weight:500;color:var(--white)}
.process-sub{left:0;width:1200px;top:1485px;text-align:center;font-size:17px;color:#d8def0}
.process-copy{left:150px;width:900px;top:1527px;text-align:center;font-size:14px;line-height:26px;color:#d8def0}
.step{left:708px;font-family:"Mulish",sans-serif;font-style:italic;font-size:17px;color:var(--white)}
.process-brand{left:170px;top:1803px;font-family:"Jost",sans-serif;font-weight:600;font-size:56px;color:var(--white)}
.remainder{left:0;top:2117px;width:1200px;height:66px;background:var(--black);color:var(--white);font-size:24px;display:flex;align-items:center;justify-content:center;font-family:"Jost",sans-serif}

/* team */
.team{left:0;top:2183px;width:1200px;height:658px;background:var(--paper)}
.team-title{left:0;width:1200px;top:2235px;text-align:center;font-size:42px;font-weight:500;color:var(--ink)}
.team-sub{left:0;width:1200px;top:2295px;text-align:center;font-size:15px;color:var(--muted)}
.member{position:absolute;width:333px;background:var(--white);box-shadow:0 6px 16px rgba(0,0,0,.12)}
.member-photo{width:100%;height:286px}
.member-band{background:var(--navy);color:var(--white);text-align:center;padding:10px 0}
.member-name{font-family:"Jost",sans-serif;font-weight:600;font-size:20px}
.member-role{font-size:14px;color:#d1d9ef;margin-top:2px}
.member-bio{padding:20px 40px;text-align:center;font-size:14px;line-height:24px}
.member-link{text-align:center;font-family:"Jost",sans-serif;font-weight:600;font-size:13px;color:var(--ink);padding-bottom:24px;letter-spacing:.5px}

/* subscribe */
.sub-title{left:0;width:1200px;top:2915px;text-align:center;font-size:42px;font-weight:500;color:var(--ink)}
.sub-sub{left:0;width:1200px;top:2982px;text-align:center;font-size:34px;color:var(--muted)}
.email-field{left:256px;top:3068px;width:468px;height:59px;border-radius:30px;background:var(--white);box-shadow:0 3px 10px rgba(0,0,0,.15);display:flex;align-items:center;justify-content:space-between;padding:0 30px;font-size:14px;color:var(--muted)}

/* contact */
.contact{left:0;top:3190px;width:1200px;height:366px;background:linear-gradient(90deg,#1a2232 0%,#323c4d 50%,#5a6371 100%)}
.contact-panel{left:78px;top:3190px;width:373px;height:366px;background:rgba(12,42,110,.85)}
.contact-title{left:125px;top:3232px;font-size:40px;font-weight:500;color:var(--white)}
.contact-row{left:128px;display:flex;gap:18px;color:var(--white);font-size:14px;line-height:22px;font-style:italic}
.contact-row svg{flex:none;margin-top:3px}

/* footer */
.site-footer{left:0;top:3556px;width:1200px;height:103px;background:var(--navy)}
.foot-nav{right:78px;top:3586px;display:flex;gap:14px;color:var(--white);font-size:14px}
.foot-nav span.sep{color:#7f94c8}
.copyright{right:78px;top:3618px;color:#c9d2ea;font-size:13px}
</style>
</head>
<body>

<header class="abs site-header">
  <div class="abs brand" style="left:78px;top:40px"><span class="brand-dot"></span>Quorbelline</div>
  <nav class="abs main-nav"><span>Home</span><span>About Us</span><span>Process</span><span>Executive Team</span><span>Contact Us</span></nav>
  <div class="pill pill-outline" style="left:955px;top:37px;width:168px;height:54px;font-size:19px">Download</div>
</header>

<section class="abs hero" role="img" aria-label="Photo of two business people reviewing documents in a bright office"></section>
<svg class="abs" style="left:28px;top:385px" width="20" height="50" viewBox="0 0 20 50"><path d="M16 2 L4 25 L16 48" stroke="rgba(255,255,255,.5)" stroke-width="2" fill="none"/></svg>
<svg class="abs" style="left:1152px;top:385px" width="20" height="50" viewBox="0 0 20 50"><path d="M4 2 L16 25 L4 48" stroke="rgba(255,255,255,.5)" stroke-width="2" fill="none"/></svg>
<h1 class="abs hero-title">Digital Assest<br>Management</h1>
<p class="abs hero-copy">Quorbelline enable companies and investors to facilities business operation in modern digital world, including asset management on hedge fund strategy model.</p>
<div class="pill pill-solid" style="left:78px;top:480px;width:208px;height:60px;font-size:20px">Contact Us</div>

<svg class="abs info-band" width="1200" height="262" viewBox="0 0 1200 262"><polygon points="0,0 1200,0 1200,165 0,262" fill="#0c2a6e"/></svg>
<svg class="abs" style="left:78px;top:730px" width="104" height="110" viewBox="0 0 104 110"><path d="M52 4 V72 M28 50 L52 74 L76 50" stroke="#fff" stroke-width="4" fill="none"/><path d="M4 64 V104 H100 V64" stroke="#fff" stroke-width="4" fill="none"/></svg>
<h2 class="abs heading info-title">Fore More Information</h2>
<p class="abs info-copy">Quorbelline process and manages on hedge fund strategy models which invests in a diversified portfolio of blockchain tokens. Blockchain tokens are emerging which add a monetary.</p>
<div class="pill pill-outline" style="left:851px;top:757px;width:272px;height:52px;font-size:17px">Download Whitepaper</div>

<h2 class="abs heading def-title">Defination of Quorbelline</h2>
<div class="abs def-copy">
  <p>Quorbelline process and manages on hedge fund strategy models which invests in a diversified portfolio of blockchain tokens. Blockchain tokens are emerging which add a monetary incentive layer to p2p protocols and facilitate equity crowdfunding that anyone in the world can participate in.</p>
  <p>This means open source software developers can monetize their networks at the protocol level and users of the network are the equity owners of the network. For this conditions, returns will go to holders of the tokens.</p>
</div>
<div class="pill pill-solid" style="left:78px;top:1258px;width:192px;height:58px;font-size:20px">Know More</div>
<div class="abs def-media" role="img" aria-label="Illustration of a hand touching glowing cryptocurrency coin icons" style="background:linear-gradient(135deg,#2a2f38 0%,#6b7180 45%,#3b6fc9 75%,#1d2a45 100%);border-right:6px solid var(--navy);border-top:6px solid var(--navy)"></div>

<section class="abs process" role="img" aria-label="Dark blue photo of hanging light bulbs behind the process chart"></section>
<h2 class="abs heading process-title">Our Process</h2>
<div class="abs process-sub">Hedge Fund Model</div>
<p class="abs process-copy">Quorbelline run on closed-end fund (CEF) model which offers its shares to investors and utilize the fund to speculate and invest in the innovative blockchain tokens. Quorbelline will charge an upfront annual operation fee 4% of the money raised during the ICO. After that, the fund will charge a quarterly performance of 50% on the net profit made.</p>
<svg class="abs" style="left:0;top:1630px" width="1200" height="440" viewBox="0 0 1200 440">
  <g stroke="#fff" stroke-width="3" fill="none">
    <line x1="640" y1="19" x2="640" y2="414"/>
    <line x1="477" y1="216" x2="640" y2="216"/>
    <line x1="640" y1="19" x2="690" y2="19"/><line x1="640" y1="116" x2="690" y2="116"/><line x1="640" y1="216" x2="690" y2="216"/><line x1="640" y1="316" x2="690" y2="316"/><line x1="640" y1="414" x2="690" y2="414"/>
    <circle cx="640" cy="19" r="9" fill="#0c2a6e"/><circle cx="640" cy="116" r="9" fill="#0c2a6e"/><circle cx="640" cy="216" r="9" fill="#0c2a6e"/><circle cx="640" cy="316" r="9" fill="#0c2a6e"/><circle cx="640" cy="414" r="9" fill="#0c2a6e"/>
    <circle cx="477" cy="216" r="10" fill="#0c2a6e"/>
  </g>
  <g fill="#fff"><path d="M684 13 L694 19 L684 25Z"/><path d="M684 110 L694 116 L684 122Z"/><path d="M684 210 L694 216 L684 222Z"/><path d="M684 310 L694 316 L684 322Z"/><path d="M684 408 L694 414 L684 420Z"/></g>
</svg>
<div class="abs process-brand">Quorbelline</div>
<div class="abs step" style="top:1638px">50 % of net profit is distributed to investors</div>
<div class="abs step" style="top:1735px">0 – 5 % net profit &gt; 0% performance fee</div>
<div class="abs step" style="top:1835px">5 – 10% net profit &gt; 5% performance fee</div>
<div class="abs step" style="top:1935px">10-15 % net profit &gt; 13% performance fee</div>
<div class="abs step" style="top:2033px">&gt; 15% net profit &gt; 15% performance fee</div>
<div class="abs remainder">The remainder ( 50% minus performance fee, so at least 35%) is reinvested</div>

<section class="abs team"></section>
<h2 class="abs heading team-title">Meet Our Executive Team</h2>
<div class="abs team-sub">We Are Ready To Help You</div>
<article class="member" style="left:78px;top:2402px">
  <div class="member-photo" role="img" aria-label="Portrait photo of the director" style="background:linear-gradient(180deg,#4a4038,#2c2a2c)"></div>
  <div class="member-band"><div class="member-name">Daravin Kolsupak</div><div class="member-role">Director</div></div>
  <p class="member-bio">Lorem Ipsum is simply dummy text of the printing and typesetting</p>
</article>
<article class="member" style="left:434px;top:2341px">
  <div class="member-photo" role="img" aria-label="Portrait photo of the technical advisor" style="height:280px;background:linear-gradient(180deg,#b9d6c4,#8fb3a6)"></div>
  <div class="member-band"><div class="member-name">Nathee Prasert</div><div class="member-role">Technical advisor</div></div>
  <p class="member-bio">Lorem Ipsum is simply dummy text of the printing and typesetting industry. Lorem Ipsum has been the.</p>
  <div class="member-link">VIEW PROFILE &nbsp;➔</div>
</article>
<article class="member" style="left:788px;top:2402px">
  <div class="member-photo" role="img" aria-label="Portrait photo of the marketing consultant" style="background:linear-gradient(180deg,#7a3a22,#3a1a12)"></div>
  <div class="member-band"><div class="member-name">Kittipol Sornwanich</div><div class="member-role">Marketing Consultant</div></div>
  <p class="member-bio">Lorem Ipsum is simply dummy text of the printing and typesetting</p>
</article>

<h2 class="abs heading sub-title">If You Are Interested In Our Quorbelline</h2>
<div class="abs heading sub-sub">Subscribe Our Newsletter</div>
<div class="abs email-field"><span>Enter Eamil</span>
  <svg width="24" height="18" viewBox="0 0 24 18"><rect x="1" y="1" width="22" height="16" rx="2" fill="none" stroke="#0c2a6e" stroke-width="2"/><path d="M1 2 L12 10 L23 2" fill="none" stroke="#0c2a6e" stroke-width="2"/></svg>
</div>
<div class="pill pill-solid" style="left:735px;top:3068px;width:210px;height:59px;font-size:20px">Subscribe</div>

<section class="abs contact" role="img" aria-label="Photo of hands typing on a laptop keyboard"></section>
<div class="abs contact-panel"></div>
<h2 class="abs heading contact-title">Contact Us</h2>
<div class="abs contact-row" style="top:3312px">
  <svg width="18" height="24" viewBox="0 0 18 24"><path d="M9 0C4 0 0 4 0 9c0 6 9 15 9 15s9-9 9-15c0-5-4-9-9-9z" fill="#fff"/><circle cx="9" cy="9" r="3.5" fill="#0c2a6e"/></svg>
  <div>Suite 08-12, 9/F, East Wing,<br>Meridale Trade Centre, Harbourview,<br>42, Lantern Quay Road, Harbour<br>District, Kowloon.</div>
</div>
<div class="abs contact-row" style="top:3436px">
  <svg width="18" height="18" viewBox="0 0 24 24"><path d="M6.6 10.8a15 15 0 006.6 6.6l2.2-2.2a1 1 0 011-.25 11.4 11.4 0 003.6.57 1 1 0 011 1V20a1 1 0 01-1 1A17 17 0 013 4a1 1 0 011-1h3.5a1 1 0 011 1c0 1.25.2 2.45.57 3.57a1 1 0 01-.25 1z" fill="#fff"/></svg>
  <div>555 204 3187</div>
</div>
<div class="abs contact-row" style="top:3476px">
  <svg width="18" height="14" viewBox="0 0 24 18"><rect width="24" height="18" rx="2" fill="#fff"/><path d="M1 2 L12 10 L23 2" fill="none" stroke="#0c2a6e" stroke-width="2"/></svg>
  <div>info@quorbelline.io</div>
</div>

<footer class="abs site-footer">
  <div class="abs brand" style="left:78px;top:34px;font-size:26px"><span class="brand-dot"></span>Quorbelline</div>
</footer>
<nav class="abs foot-nav"><span>Home</span><span class="sep">|</span><span>About Us</span><span class="sep">|</span><span>Process</span><span class="sep">|</span><span>Executive Team</span><span class="sep">|</span><span>Contact Us</span></nav>
<div class="abs copyright">©<b>Quorbelline</b> - 2017. All Rights Reserved.</div>

</body>
</html>
```